Biz Card

MARKETING today is the most rapidly changing business discipline. Media options to reach customers, actual customer preferences and consumer buying decisions change by the minute . . . no, by the second. The behavioral data generated by all aspects of the business and the new technologies that put the data to work together produce the potential to generate business intelligence and guide smart resource allocation to influence purchase and retention. However, to realize this potential, marketing professionals at all levels and in all organizations must continuously improve their skills not just from on-the-job training but by learning from masters in the field. The Bright Horizon Guild is the training center that serves this professional development need.model logos:msi.orgama.orgcontentmarketinginstitute.comBook covers on MarketingMetrics, Marketing Anaytics
Industry/Entity Type
Business
Contact Information for Business Card
Roy A. YoungCEOMarketing Science Academyphone: 310-601-4755email: roy@marketingscience.comAddress:437 South Rexford DriveBeverly Hills, CA 89377
Look and feel
Each slider illustrates characteristics of the customer's brand and the style your logo design should communicate.

```html
<!DOCTYPE html>
<html lang="en">
<head>
<meta charset="utf-8">
<title>Bright Horizon Guild – Business Card</title>
<link rel="stylesheet" href="https://fonts.googleapis.com/css2?family=Open+Sans:wght@400;600;700&display=swap">
<style>
  :root {
    --orange: #f6891f;
    --ink: #1a1a1a;
    --text: #2b2b2b;
    --paper: #ffffff;
    --backdrop: #e6e4e0;
    --rule: #3a3a3a;
  }
  * { box-sizing: border-box; margin: 0; padding: 0; }
  html, body { width: 1200px; height: 1198px; overflow: hidden; }
  body {
    background: var(--backdrop);
    font-family: "Open Sans", Arial, sans-serif;
    color: var(--text);
    display: flex;
    flex-direction: column;
    align-items: center;
    justify-content: center;
    gap: 70px;
  }
  .card {
    width: 760px;
    height: 434px;
    box-shadow: 0 10px 30px rgba(0,0,0,0.15);
    position: relative;
  }
  .card--front {
    background: var(--paper);
    display: flex;
    align-items: center;
    padding: 0 60px 0 90px;
  }
  .card--back {
    background: var(--orange);
    display: flex;
    align-items: center;
    justify-content: center;
  }
  .brand {
    display: flex;
    align-items: center;
    gap: 18px;
  }
  .brand__mark {
    width: 34px;
    height: 34px;
    background: var(--orange);
    flex: none;
  }
  .card--back .brand__mark { background: var(--paper); width: 44px; height: 44px; }
  .brand__name {
    font-weight: 700;
    color: var(--ink);
    text-transform: uppercase;
    line-height: 1.1;
    font-size: 30px;
    letter-spacing: 0.5px;
  }
  .card--back .brand__name { font-size: 42px; }
  .divider {
    width: 1px;
    height: 170px;
    background: var(--rule);
    margin: 0 44px 0 50px;
    flex: none;
  }
  .contact { display: flex; flex-direction: column; }
  .contact__name { font-size: 24px; font-weight: 600; color: var(--ink); }
  .contact__title { font-size: 17px; color: var(--orange); margin-top: 2px; margin-bottom: 26px; }
  .contact__list { list-style: none; font-size: 16px; line-height: 1.6; }
  .contact__list li { display: flex; align-items: flex-start; gap: 10px; }
  .contact__list svg { width: 15px; height: 15px; margin-top: 5px; flex: none; fill: var(--orange); }
  .contact__list .indent { padding-left: 25px; }
</style>
</head>
<body>
  <section class="card card--front">
    <div class="brand">
      <span class="brand__mark"></span>
      <div class="brand__name">Bright<br>Horizon<br>Guild</div>
    </div>
    <div class="divider"></div>
    <div class="contact">
      <p class="contact__name">Neil P. Barton</p>
      <p class="contact__title">CEO</p>
      <ul class="contact__list">
        <li>
          <svg viewBox="0 0 16 16" aria-hidden="true"><path d="M3 1h3l1.5 4-2 1.3a8 8 0 0 0 4.2 4.2L11 8.5l4 1.5v3a2 2 0 0 1-2 2A12 12 0 0 1 1 3a2 2 0 0 1 2-2z"/></svg>
          <span>310-555-0182</span>
        </li>
        <li>
          <svg viewBox="0 0 16 16" aria-hidden="true"><path d="M1 3h14v10H1z M1 3l7 6 7-6" fill="var(--orange)"/><path d="M1.5 3.5l6.5 5.5 6.5-5.5" fill="none" stroke="#fff" stroke-width="1.3"/></svg>
          <span>neil@brighthorizonguild.com</span>
        </li>
        <li>
          <svg viewBox="0 0 16 16" aria-hidden="true"><path d="M8 0a5.5 5.5 0 0 0-5.5 5.5C2.5 10 8 16 8 16s5.5-6 5.5-10.5A5.5 5.5 0 0 0 8 0zm0 7.7a2.2 2.2 0 1 1 0-4.4 2.2 2.2 0 0 1 0 4.4z"/></svg>
          <span>912 North Calloway Lane</span>
        </li>
        <li class="indent">Beverly Hills, CA 89377</li>
      </ul>
    </div>
  </section>

  <section class="card card--back">
    <div class="brand">
      <span class="brand__mark"></span>
      <div class="brand__name">Bright<br>Horizon<br>Guild</div>
    </div>
  </section>
</body>
</html>
```